Newsletter template

I am looking for 2 newsletter templates. My website is in Wordpress and I want to use in mailchimp for lists.

One newsletter is for local clients of design remodeling firm to be sent monthly

Second newsletter is for web store offerings to be sent weekly.

Target Market(s)

Luxury home and leisure

Industry/Entity Type

Store

Requirements
Must have
• Use logos and colors to seamlessly integrate with website,

```html
<!DOCTYPE html>
<html lang="en">
<head>
<meta charset="utf-8">
<title>Maison Lumen – Weekly Store Newsletter</title>
<link rel="stylesheet" href="https://fonts.googleapis.com/css2?family=Arimo:wght@400;700&display=swap">
<style>
  :root {
    --page: #ffffff;
    --banner: #444444;
    --banner-rule: #5a5a5a;
    --banner-label: #5e5e5e;
    --divider: #e6e6e6;
    --divider-soft: #f4f4f4;
    --badge: #dedd00;
    --accent: #1fb0cf;
    --link: #1d9fc4;
    --body: #777777;
    --ink: #3f3f3f;
    --button-grey: #808080;
    --art-light: #f2f2f2;
    --art-mid: #d9d9d9;
    --social-1: #5fb4d6;
    --social-2: #4f6aa6;
    --social-3: #d05a45;
  }
  html, body {
    margin: 0;
    padding: 0;
    width: 1200px;
    height: 888px;
    overflow: hidden;
    background: var(--page);
    font-family: "Arimo", Arial, sans-serif;
  }
  .newsletter {
    position: relative;
    width: 1200px;
    height: 888px;
  }
  .divider {
    position: absolute;
    left: 94px;
    width: 1014px;
    height: 14px;
    background: linear-gradient(to bottom, var(--divider-soft), var(--divider) 50%, var(--divider-soft));
    border-radius: 7px;
  }
  .divider--top { top: 22px; }
  .divider--mid { top: 246px; }
  .divider--low { top: 616px; }

  .hero-banner {
    position: absolute;
    left: 94px;
    top: 77px;
    width: 1014px;
    height: 129px;
    background: var(--banner);
  }
  .hero-banner__rule {
    position: absolute;
    left: 0;
    right: 0;
    top: 134px;
  }
  .hero-banner svg { position: absolute; left: 0; top: 52px; }

  .product-art {
    position: absolute;
    left: 97px;
    top: 322px;
    width: 306px;
    height: 282px;
    background: radial-gradient(ellipse at 50% 45%, var(--art-mid) 0%, var(--art-light) 55%, var(--page) 80%);
  }

  .product {
    position: absolute;
    left: 438px;
    top: 303px;
    width: 672px;
  }
  .product__badge {
    display: inline-block;
    background: var(--badge);
    color: #ffffff;
    font-weight: 700;
    font-size: 16px;
    line-height: 37px;
    padding: 0 13px;
  }
  .product__title {
    margin: 22px 0 0;
    color: var(--accent);
    font-weight: 400;
    font-size: 32px;
    line-height: 36px;
  }
  .product__text {
    margin: 20px 0 0;
    color: var(--body);
    font-size: 18.5px;
    line-height: 33px;
  }
  .product__actions {
    margin-top: 16px;
    display: flex;
    gap: 8px;
  }
  .button {
    display: inline-block;
    width: 104px;
    height: 36px;
    line-height: 36px;
    text-align: center;
    color: #ffffff;
    font-weight: 700;
    font-size: 16px;
    letter-spacing: 1px;
    text-decoration: none;
    box-shadow: 0 3px 3px rgba(0,0,0,0.18);
  }
  .button--view { background: var(--button-grey); }
  .button--buy { background: var(--accent); }

  .footer__address,
  .footer__contact {
    position: absolute;
    top: 674px;
    font-size: 19px;
    line-height: 32px;
  }
  .footer__address { left: 94px; color: var(--body); }
  .footer__contact { left: 443px; }
  .footer__contact a { color: var(--link); text-decoration: none; display: block; }

  .footer__social {
    position: absolute;
    left: 952px;
    top: 685px;
    display: flex;
    gap: 18px;
  }
  .social-dot {
    width: 38px;
    height: 38px;
    border-radius: 50%;
    box-shadow: 0 2px 3px rgba(0,0,0,0.2);
  }
  .social-dot--one { background: var(--social-1); }
  .social-dot--two { background: var(--social-2); }
  .social-dot--three { background: var(--social-3); }

  .footer__bar {
    position: absolute;
    left: 94px;
    top: 771px;
    width: 316px;
    height: 7px;
    background: var(--ink);
  }
  .footer__company {
    position: absolute;
    left: 94px;
    top: 806px;
    margin: 0;
    color: var(--ink);
    font-weight: 700;
    font-size: 26px;
  }
</style>
</head>
<body>
<main class="newsletter">
  <div class="divider divider--top"></div>

  <section class="hero-banner" aria-label="Header banner, 630 pixels wide">
    <svg width="1014" height="26" viewBox="0 0 1014 26" aria-hidden="true">
      <rect x="0" y="8" width="1014" height="10" fill="var(--banner-rule)"/>
      <polygon points="472,13 482,4 532,4 542,13 532,22 482,22" fill="var(--banner)"/>
      <text x="507" y="19" text-anchor="middle" font-family="Arimo, Arial, sans-serif" font-weight="700" font-size="17" fill="var(--banner-label)">630</text>
    </svg>
  </section>

  <div class="divider divider--mid"></div>

  <div class="product-art" role="img" aria-label="Product illustration: a stack of white books"></div>

  <article class="product">
    <span class="product__badge">SPECIAL PRICE: 8$</span>
    <h1 class="product__title">Vivamus Vivamus</h1>
    <p class="product__text">Donec porttitor quam vel purus venenatis rutrum. Nullam quam nibh, congue sed aliquet posuere, aliquam non lacus. Maecenas nec luctus neque...</p>
    <div class="product__actions">
      <a class="button button--view" href="#">VIEW</a>
      <a class="button button--buy" href="#">BUY</a>
    </div>
  </article>

  <div class="divider divider--low"></div>

  <footer>
    <div class="footer__address">
      Company adress, City, State<br>
      Phone: 1-800-0000-000
    </div>
    <div class="footer__contact">
      <a href="#">info@maisonlumen.com</a>
      <a href="#">maisonlumen.com</a>
    </div>
    <div class="footer__social" aria-label="Social links">
      <span class="social-dot social-dot--one"></span>
      <span class="social-dot social-dot--two"></span>
      <span class="social-dot social-dot--three"></span>
    </div>
    <div class="footer__bar"></div>
    <p class="footer__company">Maison Lumen Ltd.</p>
  </footer>
</main>
</body>
</html>
```